Los Angeles based Demolition, Grading, and Structural concrete Contractor in need of a Sale brochure

We are a Los Angeles-based demolition, grading, and structural concrete contractor looking for a professionally designed sales brochure that represents our company and services. The brochure should be visually appealing, easy to read, and include the following:

-Company Logo: Prominently displayed to enhance brand identity.

-Services We Offer: A clear breakdown of our key services, including demolition, grading, and structural concrete work.

-Project Scope & Capabilities: A brief explanation of the type of projects we handle (residential, commercial, industrial).

-Pricing Information: Mention that demolition services start at $20,000. This price includes complete demolition of structure, safe debris removal and hauling, site preparation for new construction.

-Contact Information: Our phone number(818.502.6617), email(contact@brovanbuildersinc.example) , and website for potential clients to reach out.

The design should reflect the professionalism and strength of our industry, using a modern, clean layout with bold colors that align with construction and demolition themes. Images of past work or stock photos representing our services are encouraged.

Final deliverables should be print-ready (PDF) and digital-friendly formats. Looking forward to creative and impactful designs!

```html
<!DOCTYPE html>
<html lang="en">
<head>
<meta charset="utf-8">
<title>Brovan Builders – Demolition Flyer</title>
<link rel="stylesheet" href="https://fonts.googleapis.com/css2?family=Oswald:wght@500;700&family=Roboto+Condensed:wght@400;700&display=swap">
<style>
  :root {
    --blue: #3a8ad8;
    --grey-text: #7d7f82;
    --dark-text: #4a4c50;
    --paper: #ececec;
    --band-grey: #b9bcc0;
    --bg: #8f9093;
    --dirt: #8a5f3f;
    --rubble: #55575b;
    --machine: #e0a526;
  }
  html, body {
    margin: 0;
    width: 1200px;
    height: 900px;
    overflow: hidden;
    background: var(--bg);
  }
  .flyer {
    position: absolute;
    left: 300px;
    top: 25px;
    width: 600px;
    height: 850px;
    background: var(--paper);
    overflow: hidden;
    font-family: "Oswald", sans-serif;
  }
  .top-band { position: absolute; left: 0; top: 0; width: 600px; height: 120px; }
  .brand {
    position: absolute; top: 125px; left: 0; width: 600px;
    display: flex; justify-content: center; align-items: center; gap: 12px;
  }
  .brand-mark { width: 22px; height: 22px; background: var(--blue); }
  .brand-name {
    font-weight: 700; font-size: 40px; color: var(--blue);
    letter-spacing: 2px; text-transform: uppercase; line-height: 1;
  }
  .rubble {
    position: absolute; right: 0; top: 170px; width: 50px; height: 300px;
    background: linear-gradient(to left, var(--rubble), rgba(85,87,91,0));
  }
  .offer { position: absolute; left: 110px; top: 192px; z-index: 2; }
  .offer-label {
    font-weight: 700; font-size: 52px; color: var(--grey-text);
    line-height: 1; text-transform: uppercase;
  }
  .offer-price {
    font-weight: 700; font-size: 104px; color: var(--blue);
    line-height: 0.95; margin-left: -6px;
  }
  .offer-list {
    list-style: none; margin: 6px 0 0; padding: 0;
    font-family: "Roboto Condensed", sans-serif; font-weight: 700;
    font-size: 19px; color: var(--dark-text); text-transform: uppercase; line-height: 1.25;
  }
  .scope {
    font-family: "Roboto Condensed", sans-serif; font-weight: 700;
    font-size: 15px; color: var(--blue); text-transform: uppercase;
    letter-spacing: 1px; margin-top: 12px;
  }
  .dirt {
    position: absolute; left: 0; top: 490px; width: 110px; height: 230px;
    background: radial-gradient(ellipse at 15% 60%, var(--dirt), rgba(138,95,63,0) 70%);
  }
  .services { position: absolute; left: 80px; top: 495px; z-index: 2; }
  .services-title {
    font-weight: 700; font-size: 34px; color: var(--grey-text);
    line-height: 1; margin-left: 26px; text-transform: uppercase;
  }
  .services-list {
    list-style: none; margin: 2px 0 0; padding: 0;
    font-weight: 700; font-size: 46px; color: var(--blue);
    line-height: 0.98; text-transform: uppercase;
  }
  .services-list .plus { color: var(--grey-text); font-weight: 500; margin-right: 4px; }
  .excavator {
    position: absolute; left: 435px; top: 500px; width: 145px; height: 280px;
    background: linear-gradient(160deg, var(--machine) 0%, #c98f1e 55%, #6b6b6b 100%);
    border-radius: 6px; z-index: 1;
  }
  .contact {
    position: absolute; left: 40px; bottom: 40px;
    display: flex; gap: 14px; align-items: stretch; z-index: 2;
  }
  .contact-bar {
    width: 34px; background: var(--blue);
    display: flex; flex-direction: column; align-items: center; gap: 8px; padding-top: 8px;
  }
  .contact-lines {
    font-family: "Roboto Condensed", sans-serif; font-weight: 700;
    font-size: 17px; color: var(--dark-text); line-height: 1.55;
  }
  .contact-web { color: var(--blue); font-size: 20px; }
</style>
</head>
<body>
  <main class="flyer">
    <svg class="top-band" viewBox="0 0 600 120" aria-hidden="true">
      <polygon points="0,0 600,0 600,95 0,20" fill="var(--band-grey)"/>
      <polygon points="0,0 600,0 600,80 0,8" fill="var(--blue)"/>
    </svg>

    <div class="brand">
      <span class="brand-mark"></span>
      <span class="brand-name">Brovan Builders</span>
    </div>

    <div class="rubble" role="img" aria-label="Broken concrete rubble along the edge"></div>

    <section class="offer">
      <div class="offer-label">Demolition</div>
      <div class="offer-price">$20,000</div>
      <ul class="offer-list">
        <li>+ Complete demolition of structure</li>
        <li>+ Safe debris removal and hauling</li>
        <li>+ Site preparation for new construction</li>
      </ul>
      <div class="scope">Residential - Commercial - Industrial</div>
    </section>

    <div class="dirt" role="img" aria-label="Scattered soil and dirt clumps"></div>

    <section class="services">
      <div class="services-title">Services</div>
      <ul class="services-list">
        <li><span class="plus">+</span>Demolition</li>
        <li><span class="plus">+</span>Grading</li>
        <li><span class="plus">+</span>Structural</li>
        <li>Concrete Work</li>
      </ul>
    </section>

    <div class="excavator" role="img" aria-label="Yellow excavator arm with digging bucket"></div>

    <section class="contact">
      <div class="contact-bar">
        <svg width="18" height="18" viewBox="0 0 24 24" aria-hidden="true">
          <path d="M6.6 10.8c1.4 2.8 3.8 5.1 6.6 6.6l2.2-2.2c.3-.3.7-.4 1-.2 1.1.4 2.3.6 3.6.6.6 0 1 .4 1 1V20c0 .6-.4 1-1 1C10.6 21 3 13.4 3 4c0-.6.4-1 1-1h3.5c.6 0 1 .4 1 1 0 1.3.2 2.5.6 3.6.1.3 0 .7-.2 1z" fill="#fff"/>
        </svg>
        <svg width="18" height="14" viewBox="0 0 24 18" aria-hidden="true">
          <rect x="1" y="1" width="22" height="16" fill="none" stroke="#fff" stroke-width="2"/>
          <polyline points="1,1 12,10 23,1" fill="none" stroke="#fff" stroke-width="2"/>
        </svg>
      </div>
      <div class="contact-lines">
        <div>818.502.6617</div>
        <div>contact@brovanbuildersinc.example</div>
        <div class="contact-web">brovanbuildersinc.example</div>
      </div>
    </section>
  </main>
</body>
</html>
```